Oil Field Service company needs professional business cards

Looking to clean up our current company business cards and look a little more professional. Brenwick Casing Services is a US based company that services the oil field. We deal with engineers, managers and oil rigs....................................................................................................................................................................................................................................................................................................................................................................................................

Target Market(s)

Oil and Gas professionals

Industry/Entity Type

Oil And Gas

Contact Information for Business Card

See attached photo as example

Font styles to use
Sans Serif

Colors
ec1f27

Requirements
Must have
• Company Logo, Name, Title, Cell, Office, Fax, Email.
• See attached photo
Nice to have
• External CRT, Internal CRT, Casing Crews, Torque Turn, Laydown Machine
Should not have
• Do not introduce any new pictures and keep it professional looking

```html
<!DOCTYPE html>
<html lang="en">
<head>
<meta charset="utf-8">
<title>Brenwick Casing Services – Business Card</title>
<link href="https://fonts.googleapis.com/css2?family=Roboto+Condensed:wght@400;700&family=Roboto:wght@400&display=swap" rel="stylesheet">
<style>
  :root {
    --brand-red: #d12320;
    --brand-red-deep: #c21d1c;
    --slate: #475866;
    --paper: #f4f4f3;
    --backdrop: #e6e6e6;
    --white: #ffffff;
    --tint: #f3d6d5;
  }
  * { box-sizing: border-box; margin: 0; padding: 0; }
  html, body {
    width: 1200px; height: 576px; overflow: hidden;
    background: var(--backdrop);
  }
  .canvas { position: relative; width: 1200px; height: 576px; }

  .card {
    position: absolute; top: 138px;
    width: 484px; height: 293px;
    border-radius: 6px; overflow: hidden;
    box-shadow: 0 2px 5px rgba(0,0,0,0.18);
  }

  /* Front */
  .card-front {
    left: 81px;
    background: linear-gradient(180deg, var(--brand-red) 0%, var(--brand-red-deep) 100%);
  }
  .front-wordmark {
    position: absolute; left: 0; right: 0; top: 104px;
    text-align: center; color: var(--white);
    font-family: "Roboto Condensed", sans-serif; font-weight: 700;
  }
  .front-wordmark .name-main { display: block; font-size: 52px; line-height: 1; letter-spacing: 1px; }
  .front-wordmark .name-sub { display: block; font-size: 15px; letter-spacing: 3px; margin-top: 10px; }

  /* Back */
  .card-back { left: 602px; background: var(--brand-red); }
  .back-shape { position: absolute; inset: 0; }

  .holder { position: absolute; left: 26px; top: 40px; color: var(--white); }
  .holder-name { font-family: "Roboto Condensed", sans-serif; font-weight: 700; font-size: 24px; line-height: 1; }
  .holder-title { font-family: "Roboto", sans-serif; font-size: 11.5px; margin-top: 6px; }

  .contact-list {
    position: absolute; left: 28px; top: 128px; list-style: none;
    font-family: "Roboto", sans-serif; font-size: 11.5px; color: var(--white);
  }
  .contact-list li { display: flex; align-items: center; height: 16.2px; }
  .contact-list svg { width: 10px; height: 10px; margin-right: 8px; fill: var(--white); flex: none; }

  .services-band {
    position: absolute; left: 0; top: 245px; width: 330px; height: 27px;
    background: var(--slate); color: var(--white);
    font-family: "Roboto Condensed", sans-serif; font-size: 12.5px;
    display: flex; align-items: center; padding-left: 26px; gap: 5px;
  }

  .back-wordmark {
    position: absolute; left: 414px; top: 146px;
    transform: translate(-50%, -50%) rotate(-90deg);
    white-space: nowrap; text-align: center; color: var(--slate);
    font-family: "Roboto Condensed", sans-serif; font-weight: 700;
  }
  .back-wordmark .name-main { display: block; font-size: 44px; line-height: 1; letter-spacing: 1px; }
  .back-wordmark .name-sub { display: block; font-size: 12px; letter-spacing: 2.5px; margin-top: 6px; }
</style>
</head>
<body>
<main class="canvas">

  <section class="card card-front" aria-label="Card front">
    <div class="front-wordmark">
      <span class="name-main">BRENWICK</span>
      <span class="name-sub">CASING SERVICES</span>
    </div>
  </section>

  <section class="card card-back" aria-label="Card back">
    <svg class="back-shape" viewBox="0 0 484 293" width="484" height="293" aria-hidden="true">
      <path d="M378 0 C 302 80, 296 200, 356 293 L484 293 L484 0 Z" fill="var(--paper)"/>
      <path d="M360 0 L376 0 C 320 64, 302 140, 312 212 C 296 140, 310 62, 360 0 Z" fill="var(--slate)"/>
    </svg>

    <div class="holder">
      <div class="holder-name">Cody Harlan</div>
      <div class="holder-title">Area Manager</div>
    </div>

    <ul class="contact-list">
      <li><svg viewBox="0 0 10 10"><path d="M2 0.5 L3.6 2.6 L2.7 3.6 Q3.8 5.8 6.3 7.2 L7.3 6.3 L9.5 7.9 L8.4 9.5 Q2.5 8.6 0.5 1.6 Z"/></svg>(555) 214-3800</li>
      <li><svg viewBox="0 0 10 10"><path d="M0.5 3 Q5 0 9.5 3 L8.5 4.3 L7 3.7 L7 2.8 Q5 2.2 3 2.8 L3 3.7 L1.5 4.3 Z M2 5 L8 5 L9 9.5 L1 9.5 Z"/></svg>(555) 417-2953</li>
      <li><svg viewBox="0 0 10 10"><path d="M2.5 0.5 H7.5 V3 H2.5 Z M0.5 3.5 H9.5 V7.5 H8 V6 H2 V7.5 H0.5 Z M2.5 6.5 H7.5 V9.5 H2.5 Z"/></svg>(555) 214-3861</li>
      <li><svg viewBox="0 0 10 10"><path d="M5 0.3 A3.6 3.6 0 0 1 8.6 3.9 C8.6 6.2 5 9.7 5 9.7 C5 9.7 1.4 6.2 1.4 3.9 A3.6 3.6 0 0 1 5 0.3 Z M5 2.5 A1.4 1.4 0 1 0 5 5.3 A1.4 1.4 0 1 0 5 2.5 Z" fill-rule="evenodd"/></svg>Redfield, OK 74060</li>
      <li><svg viewBox="0 0 10 10"><path d="M0.5 2 H9.5 V8 H0.5 Z M0.9 2.4 L5 5.6 L9.1 2.4" stroke="var(--brand-red)" stroke-width="0.8"/></svg>codyharlan@brenwickcasing.com</li>
      <li><svg viewBox="0 0 10 10"><circle cx="5" cy="5" r="4.5"/><path d="M0.5 5 H9.5 M5 0.5 C3 3, 3 7, 5 9.5 M5 0.5 C7 3, 7 7, 5 9.5" stroke="var(--brand-red)" stroke-width="0.6" fill="none"/></svg>www.brenwickcasing.com</li>
    </ul>

    <div class="services-band">
      <span>Laydown Machine</span><span>|</span><span>Casing Crew</span><span>|</span><span>Mud Tool</span><span>&nbsp;|</span><span>Torque Turn</span>
    </div>

    <div class="back-wordmark">
      <span class="name-main">BRENWICK</span>
      <span class="name-sub">CASING SERVICES</span>
    </div>
  </section>

</main>
</body>
</html>
```